Business Card Design

Online clothing womens clothing store, I sell my clothing online and at the markets.

i would like the attached picture on the front of the card and the contact information on the back.

Industry/Entity Type

Business

Contact Information for Business Card

Marlow Thread
Karen Whitfield
(Instagram symbol) _marlow_thread_
(Facebook symbol) www.fakebookexample.com/marlowthreadau/

W : www.marlowthread.example.au
E : info@marlowthread.example.au
P : 0498716204

```html
<!DOCTYPE html>
<html lang="en">
<head>
<meta charset="utf-8">
<title>Marlow Thread – Business Card</title>
<link rel="stylesheet" href="https://fonts.googleapis.com/css2?family=Oswald:wght@500&family=Open+Sans:wght@300;400&display=swap">
<style>
  :root {
    --page: #e9e7e4;
    --card-white: #ffffff;
    --brand-blue: #3a2fd6;
    --photo-light: #e4e8ea;
    --photo-mist: #c9d2d6;
    --photo-storm: #55586a;
    --photo-sea: #9fb9bd;
    --photo-skin: #d9b9a0;
    --photo-dark: #3b3a40;
    --text-light: #ffffff;
  }
  * { box-sizing: border-box; margin: 0; padding: 0; }
  html, body { width: 1200px; height: 902px; overflow: hidden; background: var(--page); }
  .canvas {
    width: 1200px; height: 902px;
    display: flex; align-items: center; justify-content: center; gap: 44px;
  }
  .card {
    width: 540px; height: 300px; position: relative; overflow: hidden;
    background: var(--card-white);
    box-shadow: 0 6px 18px rgba(0,0,0,.18);
  }

  /* Front */
  .card-front .front-photo {
    position: absolute; inset: 0;
    background:
      radial-gradient(ellipse 45% 60% at 70% 25%, var(--photo-storm) 0%, rgba(85,88,106,.55) 45%, rgba(85,88,106,0) 75%),
      radial-gradient(ellipse 30% 30% at 55% 55%, var(--photo-sea) 0%, rgba(159,185,189,0) 80%),
      linear-gradient(160deg, var(--photo-light) 0%, var(--photo-mist) 100%);
  }
  .card-front .front-name {
    position: absolute; left: 36px; bottom: 34px;
    font-family: "Oswald", sans-serif; font-weight: 500;
    font-size: 60px; letter-spacing: 3px; line-height: 1;
    color: var(--text-light); text-transform: uppercase;
  }

  /* Back */
  .card-back { background: var(--brand-blue); }
  .card-back .brand-name {
    position: absolute; left: 28px; top: 54px;
    font-family: "Open Sans", sans-serif; font-weight: 300;
    font-size: 20px; letter-spacing: 4.5px; line-height: 1;
    color: var(--text-light); text-transform: uppercase; white-space: nowrap;
  }
  .card-back .person-name {
    position: absolute; left: 28px; top: 106px;
    font-family: "Open Sans", sans-serif; font-weight: 400;
    font-size: 22px; line-height: 1.2; color: var(--text-light); white-space: nowrap;
  }
  .card-back .divider {
    position: absolute; left: 294px; top: 44px; width: 3px; height: 120px;
    background: var(--text-light);
  }
  .contact-list {
    position: absolute; left: 308px; top: 48px; list-style: none;
    font-family: "Open Sans", sans-serif; font-size: 12px; color: var(--text-light);
  }
  .contact-list li { display: flex; align-items: center; gap: 7px; height: 21px; white-space: nowrap; }
  .contact-list .icon {
    width: 13px; height: 13px; flex: none; background: var(--text-light);
    display: flex; align-items: center; justify-content: center;
  }
  .contact-list .icon svg { width: 9px; height: 9px; }
  .contact-list .icon-plain { background: none; border: 1.5px solid var(--text-light); }
  .contact-list .icon-dot { border-radius: 50%; }

  .photo-strip {
    position: absolute; left: 0; right: 0; bottom: 0; height: 128px;
    display: flex; gap: 10px; background: var(--card-white);
  }
  .photo-strip .photo { flex: 1; }
  .photo-strip .photo-a { background: linear-gradient(180deg, var(--photo-light) 0%, var(--photo-sea) 45%, var(--photo-skin) 60%, var(--photo-dark) 100%); }
  .photo-strip .photo-b { background: linear-gradient(180deg, var(--photo-light) 0%, var(--photo-sea) 50%, var(--photo-dark) 100%); }
  .photo-strip .photo-c { background: linear-gradient(180deg, var(--photo-light) 0%, var(--photo-mist) 50%, var(--photo-skin) 100%); }
</style>
</head>
<body>
<main class="canvas">
  <section class="card card-front" aria-label="Card front">
    <div class="front-photo" role="img" aria-label="Misty seaside photograph with a dark smudge of rock and surf"></div>
    <h1 class="front-name">Marlow Thread</h1>
  </section>

  <section class="card card-back" aria-label="Card back">
    <h2 class="brand-name">Marlow Thread</h2>
    <p class="person-name">Karen Whitfield</p>
    <div class="divider"></div>
    <ul class="contact-list">
      <li><span class="icon"><svg viewBox="0 0 10 10"><path d="M2 1 L4 1 L4.6 3 L3.4 3.8 Q4.5 6 6.2 6.6 L7 5.4 L9 6 L9 8 Q5 9 2.5 6 Q1 4 2 1 Z" fill="var(--brand-blue)"/></svg></span>0498716204</li>
      <li><span class="icon"><svg viewBox="0 0 10 10"><rect x="1" y="2.5" width="8" height="5.5" fill="none" stroke="var(--brand-blue)" stroke-width="1"/><path d="M1 2.5 L5 6 L9 2.5" fill="none" stroke="var(--brand-blue)" stroke-width="1"/></svg></span>info@marlowthread.example.au</li>
      <li><span class="icon icon-plain icon-dot"></span>www.marlowthread.example.au</li>
      <li><span class="icon icon-plain"></span>marlow_thread</li>
      <li><span class="icon icon-plain"></span>www.fakebookexample.com</li>
    </ul>
    <div class="photo-strip">
      <div class="photo photo-a" role="img" aria-label="Model in a dark slip dress on the beach"></div>
      <div class="photo photo-b" role="img" aria-label="Model in a black top by the sea"></div>
      <div class="photo photo-c" role="img" aria-label="Model in a blush knit sweater"></div>
    </div>
  </section>
</main>
</body>
</html>
```